Brintel Works - Fast, Efficient and Gas Mainteance for Domestic, Commercial and Industrial clients

We are in the process of purchasing a new business and would like to get a new logo and business card.
Business is a gas maintenance business that also does new gas installations.
Has been established since 1988.
Services include:
Install all types of gas appliances & equipment inc. hot water units
Maintain / repair / replace all types of gas appliances & equipment

Target Market(s)

Domestic, Commercial and Industrial clients

Industry/Entity Type

Business

Contact Information for Business Card

admin@brintelworks.com.au
07 3918 4726
Brintel Works PTY LTD

Logo Text

Gas Fitting & Plumbing Maintenance Specialists

Font styles to use
Sans Serif

Requirements
Must have
• Logo
• Business name, contact number, email address, web address
• Domestic | Commercial | Industrial Est Since 1988
Nice to have
• Possibly a black card with a flame logo to one side
Should not have
• Spelling errors

```html
<!DOCTYPE html>
<html lang="en">
<head>
<meta charset="utf-8">
<title>Brintel Works – Business Card</title>
<link rel="stylesheet" href="https://fonts.googleapis.com/css2?family=Arimo:wght@400;700&family=Open+Sans:wght@400&display=swap">
<style>
  :root {
    --page: #ffffff;
    --card-black: #000000;
    --panel-grey: #b5b6b9;
    --brand-blue: #0b5cb0;
    --brand-blue-light: #1694dc;
    --text-white: #ffffff;
    --text-dark: #111111;
    --tag-grey: #cfcfcf;
  }
  html, body {
    margin: 0;
    padding: 0;
    width: 1200px;
    height: 1200px;
    overflow: hidden;
    background: var(--page);
  }
  .canvas {
    position: relative;
    width: 1200px;
    height: 1200px;
    font-family: "Arimo", Arial, sans-serif;
  }
  .card {
    position: absolute;
    left: 244px;
    width: 804px;
    height: 446px;
    border-radius: 34px;
    overflow: hidden;
    background: var(--card-black);
  }
  .card--front { top: 130px; }
  .card--back  { top: 636px; }

  .front-name {
    position: absolute;
    left: 0;
    right: 0;
    top: 172px;
    text-align: center;
    font-weight: 700;
    font-size: 88px;
    line-height: 96px;
    letter-spacing: 1px;
    color: var(--brand-blue);
  }

  .back-panel {
    position: absolute;
    inset: 0;
  }

  .back-brand {
    position: absolute;
    left: 76px;
    top: 44px;
    width: 224px;
  }
  .back-brand__name {
    font-weight: 700;
    font-size: 43px;
    line-height: 60px;
    color: var(--brand-blue-light);
    white-space: nowrap;
  }
  .back-brand__legal {
    margin-top: 6px;
    font-size: 18px;
    letter-spacing: 0.6px;
    word-spacing: 3px;
    color: var(--text-white);
    white-space: nowrap;
  }

  .back-tagline {
    position: absolute;
    left: 75px;
    top: 390px;
    font-family: "Open Sans", Arial, sans-serif;
    font-size: 10px;
    color: var(--tag-grey);
    white-space: nowrap;
  }

  .contact-list {
    position: absolute;
    left: 405px;
    top: 258px;
    margin: 0;
    padding: 0;
    list-style: none;
  }
  .contact-list__item {
    display: flex;
    align-items: center;
    height: 39.3px;
    font-size: 22px;
    letter-spacing: 0.4px;
    word-spacing: 3px;
    color: var(--text-dark);
    white-space: nowrap;
  }
  .contact-list__icon {
    width: 22px;
    height: 22px;
    margin-right: 18px;
    flex: none;
  }
</style>
</head>
<body>
<div class="canvas">

  <section class="card card--front">
    <div class="front-name">BRINTEL</div>
  </section>

  <section class="card card--back">
    <svg class="back-panel" viewBox="0 0 804 446" width="804" height="446" aria-hidden="true">
      <path d="M500,0 C490,80 470,150 436,200 C400,250 360,280 362,330 C364,380 400,420 426,446 L804,446 L804,0 Z" fill="var(--panel-grey)"/>
      <path d="M500,0 C490,80 470,150 436,200 C400,250 360,280 362,330 C364,380 400,420 426,446" fill="none" stroke="var(--brand-blue)" stroke-width="6"/>
    </svg>

    <div class="back-brand">
      <div class="back-brand__name">BRINTEL</div>
      <div class="back-brand__legal">Brintel Works PTY LTD</div>
    </div>

    <div class="back-tagline">Domestic | Commercial | Industrial Est Since 1988</div>

    <ul class="contact-list">
      <li class="contact-list__item">
        <svg class="contact-list__icon" viewBox="0 0 24 24" aria-hidden="true">
          <path d="M12 3 L1.5 12.5 L4 12.5 L4 21 L10 21 L10 15 L14 15 L14 21 L20 21 L20 12.5 L22.5 12.5 Z" fill="var(--brand-blue)"/>
        </svg>
        Address 01, Address, City.
      </li>
      <li class="contact-list__item">
        <svg class="contact-list__icon" viewBox="0 0 24 24" aria-hidden="true">
          <path d="M6 2 L9.5 2.5 L10 8 L7.5 9.5 C8.5 13 10.5 16 13.5 18 L15.5 16 L20 18 L19.5 22 C12 22.5 4 14 4.5 4 Z" fill="var(--brand-blue)"/>
        </svg>
        07 3918 4726
      </li>
      <li class="contact-list__item">
        <svg class="contact-list__icon" viewBox="0 0 24 24" aria-hidden="true">
          <circle cx="12" cy="12" r="4" fill="none" stroke="var(--brand-blue)" stroke-width="2.6"/>
          <path d="M16 8 L16 14 C16 16.5 20.5 16.5 21 13 C22 6 17 2 12 2 C6 2 2 6.5 2 12 C2 17.5 6.5 22 12 22 C14.5 22 16.5 21.2 18 20" fill="none" stroke="var(--brand-blue)" stroke-width="2.6"/>
        </svg>
        admin@brintelworks.com.au
      </li>
      <li class="contact-list__item">
        <svg class="contact-list__icon" viewBox="0 0 24 24" aria-hidden="true">
          <g fill="none" stroke="var(--brand-blue)" stroke-width="1.8">
            <circle cx="12" cy="12" r="10"/>
            <ellipse cx="12" cy="12" rx="4.5" ry="10"/>
            <line x1="2" y1="12" x2="22" y2="12"/>
            <line x1="4" y1="7" x2="20" y2="7"/>
            <line x1="4" y1="17" x2="20" y2="17"/>
          </g>
        </svg>
        www.brintelworks.com.au
      </li>
    </ul>
  </section>

</div>
</body>
</html>
```